Quiet Hollow is a cabin in Gatlinburg, Tennessee, near the Ferncrest Ridge National Park. When our cabin was built, there was one thing more important than any other--peace. The front of our cabin is surrounded by woods. It has a huge deck with a swing, Adirondack chairs, and a love seat for relaxation. The back deck has a hot tub, a large round glass table for cocktails or dinner, and because we left no stone unturned, we have a telescope for stargazing. There are two master suites, each have a private bath with a large jetted tub, seperate shower, flat screen TV, and a door that leads to the back deck.

Industry/Entity Type

Business

Contact Information for Business Card

Quiet Hollow Vacation Rentals, LLC
871 Belford Crest Pl.
Oakland, Ky 42159
Janet M. Pruitt, Owner/Manager
(270) 614.2087

```html
<!DOCTYPE html>
<html lang="en">
<head>
<meta charset="utf-8">
<title>Quiet Hollow Vacation Rentals, LLC – Business Card</title>
<link href="https://fonts.googleapis.com/css2?family=Source+Sans+3:wght@400;600&display=swap" rel="stylesheet">
<style>
  :root {
    --backdrop: #3b3532;
    --card: #141414;
    --card-edge: #1f1f1f;
    --brand-silver: #cfcfcf;
    --accent-green: #3cbf4c;
    --accent-orange: #f28a1f;
    --divider: #3a3a3a;
    --icon-glyph: #ffffff;
  }
  * { box-sizing: border-box; margin: 0; padding: 0; }
  html, body {
    width: 1200px; height: 844px; overflow: hidden;
    background: var(--backdrop);
    font-family: "Source Sans 3", "Myriad Pro", sans-serif;
  }
  .canvas {
    position: relative; width: 1200px; height: 844px;
    display: flex; align-items: center; justify-content: center; gap: 60px;
  }
  .card {
    position: relative; width: 500px; height: 286px;
    background: var(--card);
    border: 1px solid var(--card-edge);
    box-shadow: 0 10px 30px rgba(0,0,0,.45);
    overflow: hidden;
  }
  /* Front */
  .brand {
    position: absolute; left: 40px; top: 40px; width: 420px;
    color: var(--brand-silver); font-weight: 600;
  }
  .brand-name { font-size: 40px; line-height: 1; letter-spacing: 1px; text-transform: uppercase; }
  .brand-sub { font-size: 21px; line-height: 1.1; margin-top: 4px; text-transform: uppercase; letter-spacing: .5px; }
  .holder {
    position: absolute; left: 40px; top: 166px; width: 200px; text-align: right;
  }
  .holder-name { color: var(--accent-green); font-size: 21px; font-weight: 600; line-height: 1.1; }
  .holder-title { color: var(--accent-orange); font-size: 14px; line-height: 1.2; }
  .holder-address { color: var(--accent-green); font-size: 15px; line-height: 1.2; margin-top: 14px; }
  .divider {
    position: absolute; left: 258px; top: 158px; width: 1px; height: 96px;
    background: var(--divider);
  }
  .contacts {
    position: absolute; left: 274px; top: 171px; list-style: none;
  }
  .contacts li {
    display: flex; align-items: center; gap: 8px;
    color: var(--accent-green); font-size: 14px; line-height: 1; height: 23px;
    white-space: nowrap;
  }
  .contact-icon {
    width: 16px; height: 16px; background: var(--accent-orange); border-radius: 2px;
    display: flex; align-items: center; justify-content: center; flex: none;
  }
  /* Back */
  .card-back { display: flex; flex-direction: column; align-items: center; justify-content: center; }
  .back-mark {
    width: 78px; height: 78px; border-radius: 50%;
    border: 2px solid #444; margin-bottom: 16px;
  }
  .back-brand { color: var(--brand-silver); font-weight: 600; text-align: center; text-transform: uppercase; }
  .back-brand .brand-name { font-size: 32px; letter-spacing: 1px; line-height: 1; }
  .back-brand .brand-sub { font-size: 16px; margin-top: 4px; }
</style>
</head>
<body>
<main class="canvas">
  <section class="card card-front" aria-label="Business card front">
    <div class="brand">
      <div class="brand-name">Quiet Hollow</div>
      <div class="brand-sub">Vacation Rentals, LLC</div>
    </div>
    <div class="holder">
      <div class="holder-name">Janet M. Pruitt</div>
      <div class="holder-title">Owner/Manager</div>
      <div class="holder-address">871 Belford Crest Pl.<br>Oakland, Ky 42159</div>
    </div>
    <div class="divider"></div>
    <ul class="contacts">
      <li>
        <span class="contact-icon"><svg width="10" height="10" viewBox="0 0 10 10"><path d="M2 1h2l1 2-1.2 1a5 5 0 0 0 2.2 2.2L7 5l2 1v2a1 1 0 0 1-1 1A7 7 0 0 1 1 2a1 1 0 0 1 1-1z" fill="var(--icon-glyph)"/></svg></span>
        (270) 614.2087
      </li>
      <li>
        <span class="contact-icon"><svg width="10" height="10" viewBox="0 0 10 10"><rect x=".5" y="2" width="9" height="6" fill="none" stroke="var(--icon-glyph)"/><path d="M.5 2 5 5.5 9.5 2" fill="none" stroke="var(--icon-glyph)"/></svg></span>
        stay@quiethollow.com
      </li>
      <li>
        <span class="contact-icon"><svg width="10" height="10" viewBox="0 0 10 10"><path d="M4 6 6 4M3.5 4.5 2 6a1.4 1.4 0 0 0 2 2l1.5-1.5M6.5 5.5 8 4a1.4 1.4 0 0 0-2-2L4.5 3.5" fill="none" stroke="var(--icon-glyph)" stroke-width="1.1" stroke-linecap="round"/></svg></span>
        www.quiethollow.com
      </li>
    </ul>
  </section>

  <section class="card card-back" aria-label="Business card back">
    <div class="back-mark"></div>
    <div class="back-brand">
      <div class="brand-name">Quiet Hollow</div>
      <div class="brand-sub">Vacation Rentals, LLC</div>
    </div>
  </section>
</main>
</body>
</html>
```